Support People to improve their image and well-being by provided personalised advise

We need a design for business cards that could be used for production on plano press. We build a new business in our region for advising mostly women (also men though) on style embracing several aspects including fashion, style, self-confidence and ultimately your internal and external image. The business card should be "classy", "french-style". The business is located in the french -speaking part of Switzerland, close to France. The name of the company is Lomu Grace

Target Market(s)

Service fees won't be cheap (medium to premium) thus we target mid-class to upper-class women (1st target) and men (2nd target)

Industry/Entity Type

Life Coaching

Contact Information for Business Card

Conseil en Image

+41 76 418 63 07
tovasel@lomu-grace.example
linkedin.example/in/sel-moran-tova

Logo Text

Lomu Grace

Colors

Designer to choose colors to be used in the design.

```html
<!DOCTYPE html>
<html lang="fr">
<head>
<meta charset="utf-8">
<title>Lomu Grace – Cartes de visite</title>
<link href="https://fonts.googleapis.com/css2?family=Questrial&display=swap" rel="stylesheet">
<style>
  :root {
    --backdrop: #bcbcbc;
    --rose: #d66a6a;
    --rose-deep: #c96161;
    --charcoal: #33383b;
    --paper: #f4f4f2;
    --ink: #2f3336;
  }
  * { margin: 0; padding: 0; box-sizing: border-box; }
  html, body {
    width: 1200px; height: 576px; overflow: hidden;
    background: var(--backdrop);
    font-family: "Questrial", "Century Gothic", sans-serif;
  }
  .canvas { position: relative; width: 1200px; height: 576px; }

  .card {
    position: absolute;
    top: 138px;
    height: 293px;
    border-radius: 15px;
    overflow: hidden;
  }
  .card-front {
    left: 82px; width: 484px;
    background: linear-gradient(180deg, var(--rose) 0%, var(--rose-deep) 100%);
    display: flex; align-items: center; justify-content: center;
  }
  .card-back {
    left: 602px; width: 481px;
    background: var(--paper);
  }

  .brand-name {
    color: var(--ink);
    font-weight: 400;
    letter-spacing: 0.5px;
    white-space: nowrap;
  }
  .card-front .brand-name { font-size: 38px; margin-top: 8px; }
  .card-back .brand-name {
    position: absolute; left: 256px; top: 60px;
    font-size: 30px;
  }

  .holder {
    position: absolute; left: 29px; top: 81px;
  }
  .holder-name {
    color: var(--rose);
    font-size: 19px;
    line-height: 1;
  }
  .holder-role {
    color: var(--ink);
    font-size: 12px;
    margin-top: 6px;
  }

  .contact-list {
    position: absolute; left: 29px; top: 216px;
    list-style: none;
  }
  .contact-item {
    display: flex; align-items: center;
    height: 17.5px;
    font-size: 12.5px;
    color: var(--ink);
  }
  .contact-icon {
    width: 10px; height: 10px;
    margin-right: 14px;
    fill: var(--rose);
  }

  .footer-bands {
    position: absolute; left: 0; bottom: 0;
    width: 481px; height: 30px;
  }
  .band-rose { fill: var(--rose); }
  .band-charcoal { fill: var(--charcoal); }
</style>
</head>
<body>
<main class="canvas">

  <section class="card card-front" aria-label="Recto de la carte">
    <span class="brand-name">Lomu Grace</span>
  </section>

  <section class="card card-back" aria-label="Verso de la carte">
    <div class="holder">
      <p class="holder-name">Elise Marnot Vey</p>
      <p class="holder-role">Conseil en Image</p>
    </div>

    <span class="brand-name">Lomu Grace</span>

    <ul class="contact-list">
      <li class="contact-item">
        <svg class="contact-icon" viewBox="0 0 10 10" aria-hidden="true">
          <path d="M1 3.2C1 2 2.5 1.2 5 1.2S9 2 9 3.2V4H7V3.2H3V4H1Z"/>
          <path d="M2.4 4.6h5.2L9 8.8H1Z"/>
        </svg>
        <span>+41 76 418 63 07</span>
      </li>
      <li class="contact-item">
        <svg class="contact-icon" viewBox="0 0 10 10" aria-hidden="true">
          <path d="M0.5 2h9v6h-9Z M1.3 2.6 5 5.6 8.7 2.6" stroke="#f4f4f2" stroke-width="0.8"/>
        </svg>
        <span>tovasel@lomu-grace.example</span>
      </li>
      <li class="contact-item">
        <svg class="contact-icon" viewBox="0 0 10 10" aria-hidden="true">
          <circle cx="5" cy="5" r="4.5"/>
          <path d="M0.5 5h9M5 0.5v9M2 2.6h6M2 7.4h6" stroke="#f4f4f2" stroke-width="0.7" fill="none"/>
          <ellipse cx="5" cy="5" rx="2" ry="4.5" stroke="#f4f4f2" stroke-width="0.7" fill="none"/>
        </svg>
        <span>www.lomu-grace.example</span>
      </li>
    </ul>

    <svg class="footer-bands" viewBox="0 0 481 30" preserveAspectRatio="none" aria-hidden="true">
      <rect class="band-rose" x="0" y="19" width="260" height="11"/>
      <path class="band-charcoal" d="M230 30 C245 18 250 2 268 2 H481 V30 Z"/>
    </svg>
  </section>

</main>
</body>
</html>
```